Business Card Design of an established Waste Management, Plastic Recycling and Renewable Energy Comp

We are looking for business card design for plastic card with holograms (Very similar to credit card). I will provide our logo (Quenbys). So the name on the business card will be our logo )Quenbys) + Environmental next to it, so it will read Quenbys Environmental. The font for Environmental does not to be the same as the font of the logo. The holograms will be used to display Certification hologram (In normal credit card, normally on the holograms, they show nova or kelo). I will post the design requirements from the card printing company very shortly to make sure they can use the design for the plastic card.

Target Market(s)

Companies, Government Organizations, Corporations.

Industry/Entity Type

Business

Contact Information for Business Card

Motto (Under the logo): Let's Keep It Green
Name: Leopold Maresca; Position: Business Manager; Address: Pelmore Landfill & Recycling Facility, Tressingham Rd, Carrow Flats, WA 6190; Ph: +61 8 5210 4738; Mob: +61 455 903 172; E: Leo@quenbysenvironmental-mail.com

Requirements
Must have
• Business Names: Quenbys Logo + Environmental word after the logo.
• Motto (Under the logo): Let's Keep It Green
• All the Business Card Details above.
• Hologram Logo on the lower right corner which says: ISO 14001 Certified.
• Please remember the design will be printed on plastic card Not paper. The plastic crad is the same as credit card. Hope this helps. Thank You

```html
<!DOCTYPE html>
<html lang="en">
<head>
<meta charset="utf-8">
<title>Quenbys Environmental — Business Card</title>
<link rel="stylesheet" href="https://fonts.googleapis.com/css2?family=Open+Sans:wght@400;600;700&family=Cinzel:wght@400&display=swap">
<style>
  :root {
    --brand-blue: #1ea1e0;
    --deep-blue: #2a5f93;
    --ink: #1f1f1f;
    --wordmark-grey: #58595b;
    --card-white: #ffffff;
    --backdrop: #e9ecef;
  }
  * { box-sizing: border-box; margin: 0; padding: 0; }
  html, body { width: 1200px; height: 900px; overflow: hidden; }
  body {
    background: var(--backdrop);
    font-family: "Open Sans", Arial, sans-serif;
    position: relative;
  }
  .card {
    position: absolute;
    border-radius: 14px;
    overflow: hidden;
    box-shadow: 0 6px 18px rgba(0,0,0,0.12);
  }

  /* Front */
  .card--front {
    left: 78px; top: 35px; width: 587px; height: 363px;
    background: var(--card-white);
  }
  .front__band {
    position: absolute; left: 0; top: 20px; width: 100%; height: 100px;
    background: var(--brand-blue);
  }
  .front__mark {
    position: absolute; left: 82px; top: 6px; width: 120px; height: 120px;
    border-radius: 50%; background: var(--card-white);
  }
  .cert-badge {
    position: absolute; right: 38px; top: 33px; width: 90px; height: 72px;
    border: 2px solid var(--card-white); border-radius: 8px;
  }
  .front__brand { position: absolute; left: 34px; top: 138px; }
  .wordmark {
    font-weight: 700; font-size: 52px; line-height: 1; letter-spacing: -0.5px;
    color: var(--wordmark-grey);
  }
  .descriptor {
    font-family: "Cinzel", Georgia, serif;
    font-size: 20px; letter-spacing: 3.4px; color: var(--deep-blue);
    margin-top: 12px;
  }
  .contact {
    position: absolute; right: 34px; top: 140px; text-align: right; color: var(--ink);
  }
  .contact__name { color: var(--brand-blue); font-weight: 600; font-size: 20px; line-height: 1.2; }
  .contact__role { font-size: 15px; margin-top: 2px; }
  .contact__lines { margin-top: 22px; font-size: 15px; line-height: 25px; }
  .contact__line { display: flex; justify-content: flex-end; align-items: center; gap: 8px; }
  .contact__line svg { width: 12px; height: 12px; fill: var(--brand-blue); }
  .contact__address { margin-top: 20px; font-size: 15px; line-height: 22px; }

  /* Back */
  .card--back {
    left: 390px; top: 507px; width: 565px; height: 348px;
    background: var(--brand-blue); color: var(--card-white); text-align: center;
  }
  .back__band {
    position: absolute; left: 0; top: 33px; width: 100%; height: 93px;
    background: var(--card-white);
  }
  .back__mark {
    position: absolute; left: 50%; top: 22px; width: 116px; height: 116px;
    margin-left: -58px; border-radius: 50%; background: var(--brand-blue);
  }
  .back__brand { position: absolute; left: 0; right: 0; top: 144px; }
  .back__brand .wordmark { color: var(--card-white); font-size: 50px; }
  .back__brand .descriptor { color: var(--card-white); margin-top: 10px; }
  .motto {
    position: absolute; left: 0; right: 0; top: 286px;
    font-weight: 700; font-size: 19px;
  }
</style>
</head>
<body>

<section class="card card--front" aria-label="Business card front">
  <div class="front__band"></div>
  <div class="front__mark"></div>
  <div class="cert-badge" role="img" aria-label="Certification hologram"></div>

  <div class="front__brand">
    <div class="wordmark">Quenbys</div>
    <div class="descriptor">ENVIRONMENTAL</div>
  </div>

  <div class="contact">
    <div class="contact__name">Leopold Maresca</div>
    <div class="contact__role">Business Manager</div>
    <div class="contact__lines">
      <div class="contact__line">+61 8 5210 4738
        <svg viewBox="0 0 24 24" aria-hidden="true"><path d="M6.6 10.8a15 15 0 0 0 6.6 6.6l2.2-2.2a1 1 0 0 1 1-.25 11.4 11.4 0 0 0 3.6.57 1 1 0 0 1 1 1V20a1 1 0 0 1-1 1A17 17 0 0 1 3 4a1 1 0 0 1 1-1h3.5a1 1 0 0 1 1 1c0 1.25.2 2.45.57 3.57a1 1 0 0 1-.25 1z"/></svg>
      </div>
      <div class="contact__line">+61 455 903 172
        <svg viewBox="0 0 24 24" aria-hidden="true"><path d="M7 1h10a2 2 0 0 1 2 2v18a2 2 0 0 1-2 2H7a2 2 0 0 1-2-2V3a2 2 0 0 1 2-2zm0 4v13h10V5z"/></svg>
      </div>
      <div class="contact__line">Leo@quenbysenvironmental-mail.com
        <svg viewBox="0 0 24 24" aria-hidden="true"><path d="M2 5h20v14H2zm2 2v.5l8 5 8-5V7l-8 5z"/></svg>
      </div>
    </div>
    <div class="contact__address">
      Pelmore Landfill &amp; Recycling Facility<br>
      Tressingham Rd, Carrow Flats, WA 6190
    </div>
  </div>
</section>

<section class="card card--back" aria-label="Business card back">
  <div class="back__band"></div>
  <div class="back__mark"></div>
  <div class="back__brand">
    <div class="wordmark">Quenbys</div>
    <div class="descriptor">ENVIRONMENTAL</div>
  </div>
  <div class="motto">Let's Keep It Green</div>
</section>

</body>
</html>
```